Larkspur Talent IT Recruiting firm needs a business card design for Recruiters, Sourcers, and Account

We need business cards that allow us to change all contact info, names, titles (Recruiter, Sourcer, Account Manager, Director, CEO, etc) per person since we have three offices, in three cities, Phoenix, Austin, and Las Vegas. We do recruiting and contractors for IT positions (Developers, Architects, Software Engineers, Security Engineers, Help Desk, DBAs, PMs, Scrum Masters, etc.) Our client companies are very diverse from Meridian 100 to silicone Valley type start-ups.

So, while we what hip, techie, and quirky, it still needs to be professional. Primary color we use is blue, with silver as a secondary color.

Target Market(s)

IT, Technology

Industry/Entity Type

Business

Contact Information for Business Card

Company name: Larkspur Talent, Inc.
Website: www.larkspurtalent.example
Logos for Careerloop, Blipster, and Myriada

Name, Title, Office Number, Cell Number, email

Font styles to use
Serif
Sans Serif

Colors
0455a3
d5d5d5

Requirements
Nice to have
• The grey I selected below is not necessary - but, would like silver included. I included a card design (File 3: LTI early trial example.jpg) that I had started on. It's very rough, and not quite what we're looking for, but what we did like is the logo, big, maybe a bit faded, off center, goes out of frame, etc. Still looking for other ideas - you are the pros! But, just an idea of a design element we liked.

```html
<!DOCTYPE html>
<html lang="en">
<head>
<meta charset="utf-8">
<title>Larkspur Talent — Business Card</title>
<link href="https://fonts.googleapis.com/css2?family=Open+Sans:wght@400;600;700&display=swap" rel="stylesheet">
<style>
  :root {
    --brand-blue: #0455a3;
    --silver: #d5d5d5;
    --silver-dark: #a9abae;
    --ink-grey: #5a5d61;
    --paper: #ffffff;
    --backdrop: #e9e9ea;
  }
  * { box-sizing: border-box; margin: 0; padding: 0; }
  html, body {
    width: 1200px; height: 948px; overflow: hidden;
    background: var(--backdrop);
    font-family: "Open Sans", Arial, sans-serif;
  }
  .sheet {
    position: relative; width: 1200px; height: 948px;
    display: flex; flex-direction: column; align-items: center; justify-content: center; gap: 48px;
  }
  .card {
    position: relative; width: 700px; height: 400px; overflow: hidden;
    background: var(--paper);
    box-shadow: 0 6px 18px rgba(0,0,0,.18);
  }
  .card-shape { position: absolute; inset: 0; width: 100%; height: 100%; }

  /* front */
  .brand { position: absolute; left: 40px; top: 120px; width: 300px; }
  .brand-mark { display: flex; align-items: center; gap: 14px; }
  .brand-dot { width: 40px; height: 40px; border-radius: 50%; background: var(--brand-blue); flex: none; }
  .brand-name {
    color: var(--brand-blue); font-weight: 600; font-size: 30px;
    line-height: 1.05; letter-spacing: .02em;
  }
  .tagline {
    margin-top: 14px; color: var(--ink-grey); font-size: 11.5px;
    letter-spacing: .22em; text-transform: uppercase;
  }

  .contact { position: absolute; left: 440px; top: 72px; color: var(--paper); }
  .person-name { font-weight: 700; font-size: 22px; }
  .person-title { font-size: 13px; margin-top: 2px; opacity: .92; }
  .contact-list { list-style: none; margin-top: 30px; display: grid; gap: 13px; }
  .contact-item { display: flex; align-items: center; gap: 10px; font-size: 13px; }
  .contact-icon {
    width: 18px; height: 18px; border-radius: 50%; background: var(--paper);
    display: flex; align-items: center; justify-content: center; flex: none;
  }
  .contact-icon svg { width: 11px; height: 11px; }

  /* back */
  .card--back { background: var(--brand-blue); }
  .back-mark { position: absolute; left: 50%; top: 64px; transform: translateX(-50%); text-align: center; }
  .back-circle { width: 190px; height: 190px; border-radius: 50%; background: var(--paper); margin: 0 auto; }
  .back-name { margin-top: 18px; color: var(--paper); font-weight: 600; font-size: 22px; letter-spacing: .04em; }
  .back-web {
    position: absolute; left: 0; right: 0; bottom: 28px; text-align: center;
    color: var(--paper); font-size: 14px; letter-spacing: .08em;
  }
</style>
</head>
<body>
<main class="sheet">

  <section class="card card--front" aria-label="Business card front">
    <svg class="card-shape" viewBox="0 0 700 400" preserveAspectRatio="none" aria-hidden="true">
      <path d="M300 0 C 330 150, 350 290, 420 400 L 395 400 C 330 290, 312 150, 286 0 Z" fill="var(--silver)"/>
      <path d="M300 0 C 330 150, 350 290, 420 400 L 408 400 C 340 290, 318 150, 292 0 Z" fill="var(--silver-dark)" opacity=".45"/>
      <path d="M312 0 C 342 150, 362 290, 432 400 L 700 400 L 700 0 Z" fill="var(--brand-blue)"/>
    </svg>

    <div class="brand">
      <div class="brand-mark">
        <span class="brand-dot"></span>
        <span class="brand-name">Larkspur<br>Talent</span>
      </div>
      <p class="tagline">Rising to the challenge</p>
    </div>

    <div class="contact">
      <p class="person-name">Maren Ellsworth</p>
      <p class="person-title">First Touch Embassador</p>
      <ul class="contact-list">
        <li class="contact-item">
          <span class="contact-icon"><svg viewBox="0 0 12 12"><path d="M3 1.5 L4.6 1.5 L5.4 3.6 L4.3 4.4 C4.9 5.7 6.2 7 7.6 7.7 L8.4 6.6 L10.5 7.4 L10.5 9 C10.5 9.8 9.8 10.5 9 10.5 C5.2 10.2 1.8 6.8 1.5 3 C1.5 2.2 2.2 1.5 3 1.5 Z" fill="var(--brand-blue)"/></svg></span>
          512-555-0147
        </li>
        <li class="contact-item">
          <span class="contact-icon"><svg viewBox="0 0 12 12"><rect x="1.5" y="3" width="9" height="6.5" rx="1" fill="none" stroke="var(--brand-blue)" stroke-width="1.3"/><path d="M1.8 3.4 L6 6.6 L10.2 3.4" fill="none" stroke="var(--brand-blue)" stroke-width="1.3"/></svg></span>
          maren@larkspurtalent.example
        </li>
        <li class="contact-item">
          <span class="contact-icon"><svg viewBox="0 0 12 12"><circle cx="6" cy="6" r="4.5" fill="none" stroke="var(--brand-blue)" stroke-width="1.2"/><path d="M1.5 6 H10.5 M6 1.5 C4 4 4 8 6 10.5 M6 1.5 C8 4 8 8 6 10.5" fill="none" stroke="var(--brand-blue)" stroke-width="1"/></svg></span>
          www.larkspurtalent.example
        </li>
        <li class="contact-item">
          <span class="contact-icon"></span>
          Blipster @MarenEllsworthLT
        </li>
        <li class="contact-item">
          <span class="contact-icon"></span>
          Careerloop @MarenEllsworthLT
        </li>
      </ul>
    </div>
  </section>

  <section class="card card--back" aria-label="Business card back">
    <div class="back-mark">
      <div class="back-circle"></div>
      <p class="back-name">Larkspur Talent</p>
    </div>
    <p class="back-web">www.larkspurtalent.example</p>
  </section>

</main>
</body>
</html>
```